Design an Office Mural for Electrical Engineering Company

We have a blank wall in our commercial office space that we would love to decorate with custom wallpaper. For this purpose, we are seeking a design to have printed as wallpaper and hung on the wall.

The design should include typography with our slogan "elevate your expectations". It is important that the design uses orange, charcoal and dark blue but other colours can also be incorporated. We want this graphic to appeal to our workforce of young, fun and intelligent men. You may like to include elements of engineering, electrical and automation in your graphic.

I have attached our logo for reference. You can choose whether or not to incorporate design elements from the logo but please DO NOT cut and paste the logo onto your design. I have attached examples of other murals that we like. Please use these as a reference for the style of your work.

The wall dimensions are 2m wide by 2.6m tall. Unfortunately we don't have a photo of the wall as it is under construction.

Target Market(s)

Young - Middle Aged Men, Tradesmen, Business People, Industrial Clients

Industry/Entity Type

Electrical engineering, factory automation, industrial maintenance

Colors
0054AA
0677BA
7BADD7
CADEEF
E8F1F8
F0912C
F2A743
F7CA91
FBE8D2
FDF5EE

Requirements
Must have
• Company colours (orange and charcoal), slogan "elevate your expectations"
Nice to have
• Hand lettering and illustration
Should not have
• The logo copy and pasted on the design. Stock images or any photographs.

```html
<!DOCTYPE html>
<html lang="en">
<head>
<meta charset="utf-8">
<title>Elevate Your Expectations – Office Mural</title>
<link rel="stylesheet" href="https://fonts.googleapis.com/css2?family=Bowlby+One&family=Yellowtail&display=swap">
<style>
  :root {
    --indigo: #2e3192;
    --royal: #283c9a;
    --mid-blue: #0088cc;
    --cyan: #00b0f0;
    --slate-blue: #4254a6;
    --cream: #f3e6d3;
    --orange: #f0862c;
    --orange-deep: #b8602a;
    --charcoal: #1e1a17;
  }
  html, body {
    margin: 0;
    padding: 0;
    overflow: hidden;
    background: var(--indigo);
  }
  .mural {
    position: relative;
    width: 923px;
    height: 1200px;
    overflow: hidden;
  }
  .mural__pattern {
    position: absolute;
    inset: 0;
    background:
      radial-gradient(circle at 20% 15%, var(--cyan) 0, transparent 38%),
      radial-gradient(circle at 85% 20%, var(--cyan) 0, transparent 32%),
      radial-gradient(circle at 75% 85%, var(--mid-blue) 0, transparent 35%),
      radial-gradient(circle at 25% 80%, var(--slate-blue) 0, transparent 40%),
      linear-gradient(160deg, var(--royal), var(--indigo) 55%, var(--royal));
  }
  .mural__slogan {
    position: absolute;
    inset: 0;
    width: 923px;
    height: 1200px;
  }
  .slogan__block {
    font-family: "Bowlby One", "Arial Black", sans-serif;
  }
  .slogan__extrude { fill: var(--orange); stroke: var(--charcoal); stroke-width: 3; paint-order: stroke; }
  .slogan__extrude--deep { fill: var(--orange-deep); }
  .slogan__face { fill: var(--cream); stroke: var(--charcoal); stroke-width: 3; paint-order: stroke; }
  .slogan__script {
    font-family: "Yellowtail", cursive;
    fill: var(--orange);
    stroke: var(--charcoal);
    stroke-width: 2;
    paint-order: stroke;
  }
  .slogan__script-shadow { fill: var(--orange-deep); }
</style>
</head>
<body>
<main class="mural">
  <div class="mural__pattern" role="img" aria-label="Geometric pattern of blue squares, quarter circles, triangles, stripes and dots"></div>

  <svg class="mural__slogan" viewBox="0 0 923 1200" aria-label="Elevate your expectations">
    <g class="slogan__block" font-size="152">
      <!-- ELEVATE -->
      <text class="slogan__extrude slogan__extrude--deep" x="226" y="559" textLength="488" lengthAdjust="spacingAndGlyphs">ELEVATE</text>
      <text class="slogan__extrude" x="223" y="555" textLength="488" lengthAdjust="spacingAndGlyphs">ELEVATE</text>
      <text class="slogan__face" x="218" y="547" textLength="488" lengthAdjust="spacingAndGlyphs">ELEVATE</text>
      <!-- EXPECTATIONS -->
      <text class="slogan__extrude slogan__extrude--deep" x="36" y="715" textLength="868" lengthAdjust="spacingAndGlyphs">EXPECTATIONS</text>
      <text class="slogan__extrude" x="33" y="711" textLength="868" lengthAdjust="spacingAndGlyphs">EXPECTATIONS</text>
      <text class="slogan__face" x="28" y="703" textLength="868" lengthAdjust="spacingAndGlyphs">EXPECTATIONS</text>
    </g>
    <g font-size="78" transform="rotate(-8 462 570)">
      <text class="slogan__script slogan__script-shadow" x="464" y="598" text-anchor="middle">your</text>
      <text class="slogan__script" x="460" y="593" text-anchor="middle">your</text>
    </g>
  </svg>
</main>
</body>
</html>
```